Landscape design build company door flyer

I would like this flyer to convey a high-level of professionalism for a company that is excellent with communication with their clients as well as a company that does incredible installations

Went on vacation/holiday

```html
<!DOCTYPE html>
<html lang="en">
<head>
<meta charset="utf-8">
<title>Summit Ridge Builders – Door Flyer</title>
<link href="https://fonts.googleapis.com/css2?family=Poppins:wght@400;500;600;700;800&display=swap" rel="stylesheet">
<style>
  :root{
    --navy:#0e2a3e;
    --orange:#f26a0a;
    --gold:#f4b223;
    --paper:#f2f2f2;
    --ink:#1b1b1b;
    --stage:#dedede;
  }
  *{box-sizing:border-box;margin:0;padding:0}
  html,body{width:1200px;height:1029px;overflow:hidden}
  body{background:var(--stage);font-family:"Poppins",sans-serif;position:relative}

  .flyer{position:absolute;left:220px;top:24px;width:760px;height:980px;background:var(--paper);overflow:hidden;box-shadow:0 6px 24px rgba(0,0,0,.18)}

  .hero-photo{position:absolute;left:330px;top:0;width:430px;height:460px;
    background:linear-gradient(160deg,#cfd3d4 0%,#b9a087 30%,#c89a6e 48%,#8c8f8c 62%,#4f7a38 80%,#3d6a2a 100%)}

  .hero-panel{position:absolute;left:0;top:0;width:760px;height:460px}

  .brand{position:absolute;left:0;top:0;width:330px;height:157px;display:flex;align-items:center;justify-content:center;gap:8px}
  .brand-mark{width:14px;height:14px;background:var(--orange)}
  .brand-name{font-weight:600;font-size:19px;color:var(--orange);letter-spacing:.4px}

  .headline{position:absolute;left:26px;top:196px;font-weight:800;font-size:50px;line-height:1.1;color:#fff;letter-spacing:-.5px}
  .headline .accent{color:var(--orange);display:block}

  .section-title{font-weight:800;font-size:21px;color:var(--navy);letter-spacing:-.2px}
  .section-title::after{content:"";display:block;width:60px;height:3px;background:var(--gold);border-radius:2px;margin-top:4px}

  .about{position:absolute;left:26px;top:480px;width:380px}
  .about p{margin-top:12px;font-size:11.3px;line-height:1.45;color:var(--ink);text-align:justify}

  .services{position:absolute;left:440px;top:480px;width:290px}
  .services ul{list-style:none;margin-top:12px}
  .services li{display:flex;align-items:center;gap:10px;font-size:12px;font-weight:500;color:var(--ink);margin-bottom:6px;line-height:16px}
  .services svg{flex:none}

  .works-rule{position:absolute;left:16px;right:16px;top:704px;height:2px;background:var(--gold)}
  .works-tab{position:absolute;left:290px;top:690px;width:180px;height:30px;background:var(--orange);color:#fff;font-weight:700;font-size:15px;display:flex;align-items:center;justify-content:center;letter-spacing:.3px}

  .works{position:absolute;left:26px;top:736px;right:26px;display:flex;gap:24px}
  .work{flex:1;height:118px}
  .work-deck{background:linear-gradient(160deg,#6b5a4c,#b89a88 45%,#8d7466)}
  .work-rail{background:linear-gradient(160deg,#2a2a2a,#9ea3a3 40%,#cfd1cf 70%,#5a6a55)}
  .work-garden{background:linear-gradient(160deg,#6f8a57,#8f9a8b 45%,#b6bbb8 70%,#4d6a3a)}

  .footer{position:absolute;left:0;bottom:0;width:760px;height:90px}
  .phone{position:absolute;left:26px;bottom:20px;display:flex;align-items:center;gap:12px}
  .phone-icon{width:50px;height:50px;background:var(--orange);display:flex;align-items:center;justify-content:center}
  .phone-number{font-weight:800;font-size:40px;color:#fff;letter-spacing:-.5px}
  .contact{position:absolute;left:485px;bottom:16px;font-size:13px;color:#fff;line-height:1.9}
  .contact div{display:flex;align-items:center;gap:14px}
</style>
</head>
<body>
  <main class="flyer">
    <div class="hero-photo" role="img" aria-label="Photo of a two-level cedar deck with staircase and railings beside a house, lawn in front"></div>

    <svg class="hero-panel" viewBox="0 0 760 460" aria-hidden="true">
      <polygon points="0,0 330,0 330,157 0,157" fill="var(--paper)"/>
      <polygon points="0,157 455,157 530,300 530,460 0,460" fill="var(--navy)"/>
    </svg>

    <header class="brand">
      <span class="brand-mark"></span>
      <span class="brand-name">SUMMIT RIDGE BUILDERS</span>
    </header>

    <h1 class="headline">
      LET’S CREATE<br>YOUR DREAM
      <span class="accent">OUTDOOR<br>LIVING SPACE!</span>
    </h1>

    <section class="about">
      <h2 class="section-title">ABOUT US</h2>
      <p>Discover the endless possibilities for your outdoor space with The Summit Ridge Builders Team. Our team of skilled artisans is dedicated to turning your outdoor space into a breathtaking oasis that you’ll love coming home to. Whether it’s a cozy patio for intimate gatherings, a sprawling deck to host memorable parties, or a custom paver driveway that adds instant curb appeal, our high-quality craftsmanship ensures stunning results that exceed your expectations.</p>
    </section>

    <section class="services">
      <h2 class="section-title">OUR SERVICES</h2>
      <ul>
        <li><svg width="14" height="14" viewBox="0 0 14 14"><circle cx="7" cy="7" r="7" fill="var(--orange)"/><path d="M3.8 7.2l2.1 2.1 4.3-4.4" stroke="#fff" stroke-width="1.7" fill="none"/></svg>Paver Patios</li>
        <li><svg width="14" height="14" viewBox="0 0 14 14"><circle cx="7" cy="7" r="7" fill="var(--orange)"/><path d="M3.8 7.2l2.1 2.1 4.3-4.4" stroke="#fff" stroke-width="1.7" fill="none"/></svg>Paver Driveways</li>
        <li><svg width="14" height="14" viewBox="0 0 14 14"><circle cx="7" cy="7" r="7" fill="var(--orange)"/><path d="M3.8 7.2l2.1 2.1 4.3-4.4" stroke="#fff" stroke-width="1.7" fill="none"/></svg>Retaining Walls</li>
        <li><svg width="14" height="14" viewBox="0 0 14 14"><circle cx="7" cy="7" r="7" fill="var(--orange)"/><path d="M3.8 7.2l2.1 2.1 4.3-4.4" stroke="#fff" stroke-width="1.7" fill="none"/></svg>Decks &amp; Railings</li>
        <li><svg width="14" height="14" viewBox="0 0 14 14"><circle cx="7" cy="7" r="7" fill="var(--orange)"/><path d="M3.8 7.2l2.1 2.1 4.3-4.4" stroke="#fff" stroke-width="1.7" fill="none"/></svg>Pools</li>
        <li><svg width="14" height="14" viewBox="0 0 14 14"><circle cx="7" cy="7" r="7" fill="var(--orange)"/><path d="M3.8 7.2l2.1 2.1 4.3-4.4" stroke="#fff" stroke-width="1.7" fill="none"/></svg>Outdoor Lighting</li>
        <li><svg width="14" height="14" viewBox="0 0 14 14"><circle cx="7" cy="7" r="7" fill="var(--orange)"/><path d="M3.8 7.2l2.1 2.1 4.3-4.4" stroke="#fff" stroke-width="1.7" fill="none"/></svg>Firepits &amp; Fireplaces</li>
      </ul>
    </section>

    <div class="works-rule"></div>
    <div class="works-tab">OUR WORKS</div>

    <div class="works">
      <div class="work work-deck" role="img" aria-label="Photo of composite deck steps beside a covered hot tub"></div>
      <div class="work work-rail" role="img" aria-label="Photo of a grey composite deck with black metal railing"></div>
      <div class="work work-garden" role="img" aria-label="Photo of a landscaped garden with paver path and retaining walls"></div>
    </div>

    <footer class="footer">
      <svg width="760" height="90" viewBox="0 0 760 90" aria-hidden="true" style="position:absolute;left:0;top:0">
        <rect width="760" height="90" fill="var(--navy)"/>
        <polygon points="470,0 760,0 760,90 440,90" fill="var(--orange)"/>
      </svg>
      <div class="phone">
        <span class="phone-icon">
          <svg width="26" height="26" viewBox="0 0 24 24"><path fill="#fff" d="M6.6 10.8a15.1 15.1 0 0 0 6.6 6.6l2.2-2.2c.3-.3.7-.4 1-.2 1.1.4 2.3.6 3.6.6.6 0 1 .4 1 1V20c0 .6-.4 1-1 1A17 17 0 0 1 3 4c0-.6.4-1 1-1h3.5c.6 0 1 .4 1 1 0 1.3.2 2.5.6 3.6.1.3 0 .7-.2 1z"/></svg>
        </span>
        <span class="phone-number">555-014-2286</span>
      </div>
      <div class="contact">
        <div><svg width="16" height="12" viewBox="0 0 16 12"><rect width="16" height="12" rx="1" fill="#fff"/><path d="M1 1l7 5.5L15 1" stroke="var(--orange)" stroke-width="1.4" fill="none"/></svg>info@summitridgebuild.com</div>
        <div><svg width="16" height="16" viewBox="0 0 16 16" fill="none" stroke="#fff" stroke-width="1.3"><circle cx="8" cy="8" r="7"/><ellipse cx="8" cy="8" rx="3" ry="7"/><path d="M1 8h14M2.5 4.5h11M2.5 11.5h11"/></svg>www.summitridgebuild.com</div>
      </div>
    </footer>
  </main>
</body>
</html>
```